Company website for an international IT business

We require a website for our business, Korvel Solutions. The business has two primary areas: Lanterns, which includes two machine learning/deep learning based products and IT consultancy, which is the service we provide to other businesses.

We bridge cutting-edge research to market.

STYLING:
The site can be on single page or multi-page. This is fully open to suggestion. So long as the look and feel are consistent. Currently, we have no strong preference for colors, styles or layouts.
You can find the logo of our website in the attachment “Korvel-logo.png” and “Korvel-logo-landscape.png”.

CONTENT:
You can find the text of the website in “Website-Content.pdf”, which explains the services and products of our business. The format of the text is also open to suggestion - including breaking up the text into visually appealing sections.
We would also like to include suitable images on the website so that it does not appear to be a text-heavy page. We are happy to have placeholder images on stock image sites if needed. We are open to suggestions on placing of images

ATTACHMENT:

Industry/Entity Type

It Company

Coding

Coded - Design and coding required

Number of Pages Required

1 page

Colors

Designer to choose colors to be used in the design.

Requirements
Must have
• A full description of the requirement is in the attachment "Website-Content.pdf"
• The design must have HTML/CSS, and all resources relevant (images, fonts etc)
• We are
Nice to have
• We are open to suggestions on top of the requirement, please reach out and communicate.

```html
<!DOCTYPE html>
<html lang="en">
<head>
<meta charset="utf-8">
<title>Korvel Solutions</title>
<link href="https://fonts.googleapis.com/css2?family=Montserrat:wght@400;500;600;700&family=Open+Sans:wght@400;600;700&display=swap" rel="stylesheet">
<style>
:root{
  --blue:#0b7bc0;
  --blue-dark:#0a6aa6;
  --ink:#1d1d1d;
  --text:#4a4a4a;
  --grey-band:#eeeef0;
  --white:#ffffff;
  --rule:#9a9a9a;
}
*{margin:0;padding:0;box-sizing:border-box}
html,body{width:1200px;height:3035px;overflow:hidden}
body{font-family:"Open Sans",Arial,sans-serif;color:var(--text);background:var(--white);position:relative}
.abs{position:absolute}
.brand-name{font-family:"Montserrat",Arial,sans-serif;font-weight:700;letter-spacing:1px}

/* header */
.site-header{position:absolute;left:0;top:0;width:1200px;height:101px;background:var(--white)}
.site-header .mark{left:132px;top:16px;width:76px;height:76px;border-radius:50%;background:var(--blue)}
.site-header .brand-name{left:222px;top:34px;font-size:30px;color:var(--ink)}
.call{right:130px;top:22px;display:flex;align-items:center;gap:10px;font-family:"Montserrat",Arial,sans-serif}
.call small{font-size:10px;font-weight:600;color:var(--ink);letter-spacing:.5px}
.call strong{font-size:19px;color:var(--blue);font-weight:600}
.main-nav{right:130px;top:62px;display:flex;gap:8px;font-family:"Montserrat",Arial,sans-serif;font-size:12px;font-weight:600;color:var(--ink)}
.main-nav a{padding:6px 10px;color:inherit;text-decoration:none}
.main-nav a.active{background:var(--blue);color:var(--white)}

/* hero */
.hero{left:0;top:101px;width:1200px;height:557px;background:linear-gradient(100deg,#b9c6cf 0%,#8e9aa2 30%,#5b5f60 55%,#b3b6b5 80%,#8d9192 100%)}
.hero-copy{left:788px;top:142px;color:var(--white);font-family:"Montserrat",Arial,sans-serif}
.hero-copy p{font-size:24px;font-weight:600;letter-spacing:.5px}
.hero-copy h1{font-size:64px;font-weight:600;letter-spacing:2px;line-height:1.05}
.btn{display:inline-block;background:var(--blue);color:var(--white);font-family:"Montserrat",Arial,sans-serif;font-weight:700;text-transform:uppercase;text-decoration:none}
.hero-copy .btn{margin-top:18px;padding:14px 26px;font-size:14px}
.dots{left:536px;top:488px;display:flex;gap:16px}
.dots i{width:10px;height:10px;border-radius:50%;background:var(--white)}
.dots i.on{background:var(--blue)}

/* section heads */
.section-title{font-family:"Montserrat",Arial,sans-serif;font-size:20px;font-weight:700;color:var(--blue);text-align:center;width:1200px;left:0;letter-spacing:.5px}
.section-rule{width:56px;height:2px;background:var(--rule);left:572px}

/* what */
.what-intro{left:0;width:1200px;top:774px;text-align:center;font-size:13px;line-height:20px}
.service{top:870px;width:260px;text-align:center}
.service svg{display:block;margin:0 auto}
.service h3{margin-top:30px;font-family:"Montserrat",Arial,sans-serif;font-weight:500;font-size:16px;color:var(--ink)}

/* lanterns */
.lanterns{left:0;top:1067px;width:1200px;height:569px;background:var(--grey-band)}
.card{top:1200px;width:397px}
.card .photo{width:397px;height:257px}
.card h3{margin-top:20px;font-family:"Montserrat",Arial,sans-serif;font-size:20px;font-weight:700;color:var(--blue)}
.card p{margin-top:6px;font-size:13px;line-height:19px;color:var(--ink);width:340px}
.card .btn{margin-top:12px;padding:5px 10px;font-size:10px}

/* consultancy */
.consult{left:0;top:1636px;width:1200px;height:453px;background:linear-gradient(90deg,#dfe6ea 0%,#cdd5d9 40%,#5f6c7c 62%,#2e3747 85%,#3c4658 100%)}
.consult-copy{left:223px;top:1718px;width:330px}
.consult-copy h2{font-family:"Montserrat",Arial,sans-serif;font-size:20px;font-weight:700;color:var(--blue)}
.consult-copy p{margin-top:18px;font-size:13px;line-height:20px;color:var(--ink)}
.consult-copy .btn{margin-top:18px;padding:5px 10px;font-size:10px}

/* about */
.about-photo{left:132px;top:2149px;width:431px;height:428px;background:linear-gradient(180deg,#b9c6d4 0%,#d8dde3 35%,#9a8f84 62%,#6aa7b6 78%,#c9b89a 100%)}
.about-copy{left:630px;top:2152px;width:460px}
.about-copy h2{font-family:"Montserrat",Arial,sans-serif;font-size:20px;font-weight:700;color:var(--blue)}
.about-copy .rule{width:56px;height:2px;background:var(--rule);margin-top:14px}
.about-copy .lead{margin-top:28px;font-size:13px;line-height:20px;color:var(--ink)}
.perks{list-style:none;margin-top:22px}
.perks li{display:flex;align-items:center;gap:30px;height:92px;font-size:13px;line-height:20px;color:var(--ink)}
.perks svg{flex:none}
.about-copy .btn{margin-top:20px;padding:5px 10px;font-size:10px}

/* footer */
.site-footer{left:0;top:2651px;width:1200px;height:384px;background:var(--blue);color:var(--white)}
.site-footer .mark{left:164px;top:2726px;width:76px;height:76px;border-radius:50%;background:var(--white)}
.site-footer .brand-name{left:148px;top:2812px;font-size:24px;color:var(--white)}
.foot-col h4{font-family:"Montserrat",Arial,sans-serif;font-size:13px;font-weight:700;letter-spacing:.5px;margin-bottom:18px}
.foot-col ul{list-style:none;font-size:12px;line-height:18px}
.contact li{display:flex;gap:14px;margin-bottom:18px}
.map{left:704px;top:2710px;width:363px;height:215px;background:linear-gradient(135deg,#eef0ec,#dfe3dd)}
.foot-rule{left:132px;top:2924px;width:550px;height:1px;background:rgba(255,255,255,.35)}
.copyright{left:0;width:1200px;top:2972px;text-align:left;padding-left:506px;font-size:11px}
</style>
</head>
<body>

<header class="site-header">
  <div class="abs mark"></div>
  <div class="abs brand-name">KORVEL</div>
  <div class="abs call">
    <svg width="18" height="18" viewBox="0 0 24 24"><path fill="#0b7bc0" d="M6.6 10.8a15 15 0 0 0 6.6 6.6l2.2-2.2c.3-.3.7-.4 1-.2 1.1.4 2.3.6 3.6.6.6 0 1 .4 1 1V20c0 .6-.4 1-1 1A17 17 0 0 1 3 4c0-.6.4-1 1-1h3.5c.6 0 1 .4 1 1 0 1.3.2 2.5.6 3.6.1.3 0 .7-.2 1z"/></svg>
    <small>CALL US:</small><strong>555.010.2040</strong>
  </div>
  <nav class="abs main-nav">
    <a class="active" href="#">HOME</a><a href="#">LANTERNS</a><a href="#">IT CONSULTANCY</a><a href="#">CONTACT US</a>
  </nav>
</header>

<section class="abs hero" role="img" aria-label="Photo of a truck driver climbing into the cab of a white lorry under a cloudy sky"></section>
<div class="abs hero-copy">
  <p>WELCOME TO</p>
  <h1>KORVEL</h1>
  <a class="btn" href="#">Read More</a>
</div>
<div class="abs dots"><i></i><i></i><i class="on"></i><i></i><i></i></div>

<h2 class="abs section-title" style="top:702px">WHAT IS KORVEL</h2>
<div class="abs section-rule" style="top:740px"></div>
<p class="abs what-intro">Korvel Solutions is an IT consultancy firm with a difference We can provide IT expertise<br>for your business at any stage - from initial idea to live systems</p>

<div class="abs service" style="left:200px">
  <svg width="80" height="70" viewBox="0 0 80 70" fill="none" stroke="#0b7bc0" stroke-width="3">
    <rect x="10" y="6" width="60" height="40" rx="3"/><path d="M2 52h76l-4 8H6z"/>
    <circle cx="40" cy="32" r="8"/><path d="M40 18v4M40 42v-2M26 32h4M54 32h-4M30 22l3 3M50 22l-3 3"/>
  </svg>
  <h3>Software development</h3>
</div>
<div class="abs service" style="left:470px">
  <svg width="80" height="80" viewBox="0 0 80 80" fill="none" stroke="#0b7bc0" stroke-width="3">
    <circle cx="40" cy="40" r="15"/><path d="M25 40h30M40 25v30M30 30c5 4 15 4 20 0M30 50c5-4 15-4 20 0"/>
    <path d="M40 4v14M40 62v14M4 40h14M62 40h14M14 14l10 10M66 14 56 24M14 66l10-10M66 66 56 56"/>
    <path d="M36 8l4-4 4 4M36 72l4 4 4-4M8 36l-4 4 4 4M72 36l4 4-4 4"/>
  </svg>
  <h3>IOT System Design</h3>
</div>
<div class="abs service" style="left:740px">
  <svg width="80" height="80" viewBox="0 0 80 80">
    <path fill="#0b7bc0" d="M40 6c-17 0-28 12-28 27 0 8 3 13 7 18v23h28v-9h10c3 0 5-2 5-5v-9l6-2-6-12c0-18-9-31-22-31z"/>
    <circle cx="38" cy="32" r="11" fill="none" stroke="#fff" stroke-width="4" stroke-dasharray="5 3"/>
    <circle cx="38" cy="32" r="5" fill="#fff"/>
  </svg>
  <h3>Machine learning solutions</h3>
</div>

<section class="abs lanterns"></section>
<h2 class="abs section-title" style="top:1109px">LANTERNS</h2>
<div class="abs section-rule" style="top:1147px"></div>

<article class="abs card" style="left:180px">
  <div class="photo" role="img" aria-label="Photo of a driver in a high-visibility vest at the open door of a truck cab" style="background:linear-gradient(90deg,#2a4fa8 0%,#3b63be 30%,#c9cdd2 55%,#8d9399 100%)"></div>
  <h3>HALDEN</h3>
  <p>The primary cause of accidents on the road are caused by human error.</p>
  <a class="btn" href="#">Read More</a>
</article>
<article class="abs card" style="left:621px">
  <div class="photo" role="img" aria-label="Photo of a hand touching a glowing digital data screen" style="background:linear-gradient(135deg,#0c1a4a 0%,#3b2a8c 40%,#b43c9c 62%,#1c5fa8 100%)"></div>
  <h3>WHEELWISE</h3>
  <p>Wheelwise is a machine learning system that tracks and analyzes live used car trading</p>
  <a class="btn" href="#">Read More</a>
</article>

<section class="abs consult" role="img" aria-label="Photo of two businessmen in suits reviewing a document at a bright office table"></section>
<div class="abs consult-copy">
  <h2>IT CONSULTANCY</h2>
  <p>There are many variations of passages of Lorem Ipsum available, but the majority have suffered alteration in some form, by injected humour, or randomised words which don't look even slightly believable.</p>
  <a class="btn" href="#">Read More</a>
</div>

<div class="abs about-photo" role="img" aria-label="Photo of a skyline of modern towers above a beach and turquoise sea"></div>
<div class="abs about-copy">
  <h2>ABOUT US</h2>
  <div class="rule"></div>
  <p class="lead">Korvel Solutions is an IT consultancy firm with a difference We can provide IT expertise for your business at any stage - from initial idea to live systems</p>
  <ul class="perks">
    <li><svg width="44" height="32" viewBox="0 0 44 32" fill="none" stroke="#8a8a8a" stroke-width="1.5"><rect x="2" y="4" width="24" height="18"/><path d="M26 10h9l6 7v5H26"/><circle cx="10" cy="25" r="4"/><circle cx="33" cy="25" r="4"/></svg><span>Acquire more development capacity<br>and get results fast</span></li>
    <li><svg width="44" height="40" viewBox="0 0 44 40" fill="none" stroke="#0b7bc0" stroke-width="1.5"><path d="M16 8h12l-3 5H19zM19 13C8 18 6 36 22 36s14-18 3-23"/><path d="M25 20c-1-2-6-2-6 1s6 2 6 5-5 3-6 1M22 17v2M22 29v2"/></svg><span>Avoid the overhead incurred by frequent<br>scaling of your development team</span></li>
    <li><svg width="44" height="40" viewBox="0 0 44 40" fill="none" stroke="#8a8a8a" stroke-width="1.5"><circle cx="8" cy="32" r="3"/><circle cx="20" cy="18" r="3"/><circle cx="30" cy="26" r="3"/><circle cx="38" cy="8" r="3"/><path d="M10 30l8-10M22 20l6 4M32 23l5-12"/></svg><span>Reach a wide spectrum of expertise</span></li>
  </ul>
  <a class="btn" href="#">Read More</a>
</div>

<footer class="abs site-footer"></footer>
<div class="abs mark" style="left:164px;top:2726px;width:76px;height:76px;border-radius:50%;background:var(--white)"></div>
<div class="abs brand-name" style="left:148px;top:2812px;font-size:24px;color:var(--white)">KORVEL</div>

<div class="abs foot-col" style="left:352px;top:2710px;color:var(--white)">
  <h4>MENU</h4>
  <ul><li>Home</li><li>About Us</li><li>Lanterns</li><li>Consultancy</li><li>Contact Us</li></ul>
</div>
<div class="abs foot-col contact" style="left:508px;top:2716px;color:var(--white)">
  <h4>CONTACT US</h4>
  <ul>
    <li><svg width="10" height="14" viewBox="0 0 10 14"><path fill="#fff" d="M5 0a5 5 0 0 0-5 5c0 4 5 9 5 9s5-5 5-9a5 5 0 0 0-5-5zm0 7a2 2 0 1 1 0-4 2 2 0 0 1 0 4z"/></svg><span>418 Foundry Lane<br>Marlow, IL 60990</span></li>
    <li><svg width="11" height="11" viewBox="0 0 24 24"><path fill="#fff" d="M6.6 10.8a15 15 0 0 0 6.6 6.6l2.2-2.2c.3-.3.7-.4 1-.2 1.1.4 2.3.6 3.6.6.6 0 1 .4 1 1V20c0 .6-.4 1-1 1A17 17 0 0 1 3 4c0-.6.4-1 1-1h3.5c.6 0 1 .4 1 1 0 1.3.2 2.5.6 3.6.1.3 0 .7-.2 1z"/></svg><span>555.010.2040</span></li>
    <li><svg width="12" height="10" viewBox="0 0 12 10"><path fill="#fff" d="M0 0h12v10H0zm1 1.5V9h10V1.5L6 5.5z"/></svg><span>hello@korvel.example</span></li>
  </ul>
</div>
<div class="abs map" role="img" aria-label="Street map showing the office location with a red pin"></div>
<div class="abs foot-rule"></div>
<p class="abs copyright" style="color:var(--white)">Copyrights @ 2018 All Rights Reserved</p>

</body>
</html>
```